Brightfield Ventures Inc. Letterhead

Creation of attractive and eye catching letterhead for a business start-up for the construction industry. Letterhead must relate to construction, but avoid standard hammer and tools in the design.

I forgot to add some details, sorry about that. Some pertinent info: Ph: 916-555-0187 brightfieldventures.example 448 Willowmere Ave, Ste 210 Folsom, CA 95999 info@brightfieldventures.example not sure if slogan should be in there" “Connecting construction professionals to create a purpose driven industry.” must be able to be used in word. Thanks!

```html
<!DOCTYPE html>
<html lang="en">
<head>
<meta charset="utf-8">
<title>Brightfield Ventures Inc. Letterhead</title>
<link href="https://fonts.googleapis.com/css2?family=Arimo:wght@400;700&display=swap" rel="stylesheet">
<style>
  :root {
    --backdrop: #b9cce4;
    --paper: #ffffff;
    --navy: #22338f;
    --navy-deep: #1a2775;
    --brand-red: #d3222a;
    --text: #1b1b1b;
    --muted: #555a66;
    --ghost: #ebecf0;
  }
  * { box-sizing: border-box; margin: 0; padding: 0; }
  html, body {
    width: 1200px; height: 784px; overflow: hidden;
    background: var(--backdrop);
    font-family: "Arimo", Arial, sans-serif;
  }
  .letterhead {
    position: absolute; left: 338px; top: 22px;
    width: 524px; height: 740px;
    background: var(--paper);
    box-shadow: 0 4px 18px rgba(40, 60, 110, .18);
    overflow: hidden;
  }
  .brand {
    position: absolute; left: 40px; top: 38px;
    display: flex; align-items: center; gap: 8px;
    font-weight: 700; font-size: 15px; color: var(--navy);
  }
  .brand-mark { width: 11px; height: 11px; background: var(--brand-red); }
  .brand-rule {
    position: absolute; left: 40px; top: 62px;
    width: 190px; height: 2px; background: var(--brand-red);
  }
  .contact {
    position: absolute; left: 330px; top: 250px; width: 170px;
    font-style: normal;
    font-size: 7.5px; line-height: 12px; color: var(--muted);
  }
  .contact-name {
    font-weight: 700; font-size: 10.5px; color: var(--brand-red);
    margin-bottom: 4px;
  }
  .contact-line { display: flex; align-items: flex-start; gap: 6px; }
  .contact-line svg { flex: none; margin-top: 2.5px; }
  .body-copy {
    position: absolute; left: 40px; top: 96px; width: 272px;
    font-size: 8.6px; line-height: 11.6px; color: var(--text);
  }
  .body-copy p { margin-bottom: 11.6px; }
  .signature {
    position: absolute; left: 40px; top: 548px;
    width: 120px; height: 30px;
    background: linear-gradient(90deg, #f1f1f3, #e6e7ec);
    border-radius: 3px;
  }
  .ghost-name {
    position: absolute; right: 34px; top: 606px;
    font-weight: 700; font-size: 24px; color: var(--ghost);
  }
  .swoosh { position: absolute; left: 0; bottom: 0; width: 524px; height: 150px; }
</style>
</head>
<body>
  <main class="letterhead">
    <div class="brand"><span class="brand-mark"></span>Brightfield Ventures Inc.</div>
    <div class="brand-rule"></div>

    <address class="contact">
      <div class="contact-name">Brightfield Ventures Inc.</div>
      <div class="contact-line">
        <svg width="7" height="7" viewBox="0 0 10 10"><circle cx="5" cy="5" r="4.5" fill="#d3222a"/></svg>
        <span>448 Willowmere Ave, Ste 210<br>Folsom, CA 95999</span>
      </div>
      <div class="contact-line">
        <svg width="7" height="7" viewBox="0 0 10 10"><circle cx="5" cy="5" r="4.5" fill="#d3222a"/></svg>
        <span>Ph: 916-555-0187</span>
      </div>
      <div class="contact-line">
        <svg width="7" height="7" viewBox="0 0 10 10"><circle cx="5" cy="5" r="4.5" fill="#d3222a"/></svg>
        <span>916-555-0188</span>
      </div>
      <div class="contact-line">
        <svg width="7" height="7" viewBox="0 0 10 10"><circle cx="5" cy="5" r="4.5" fill="#d3222a"/></svg>
        <span>info@brightfieldventures.example</span>
      </div>
      <div class="contact-line">
        <svg width="7" height="7" viewBox="0 0 10 10"><circle cx="5" cy="5" r="4.5" fill="#d3222a"/></svg>
        <span>www.brightfieldventures.example</span>
      </div>
    </address>

    <section class="body-copy">
      <p>Lorem Ipsum is simply dummy text of the printing and typesetting industry. Lorem Ipsum has been the industry's standard dummy text ever since the 1500s, when an unknown printer took a galley of type and scrambled it to make a type specimen book. It has survived not only five centuries, but also the leap into electronic typesetting, remaining essentially unchanged. It was popularised in the 1960s with the release of Presstone sheets containing Lorem Ipsum passages, and more recently with desktop publishing software like Paginator Desk including versions of Lorem Ipsum.</p>
      <p>It is a long established fact that a reader will be distracted by the readable content of a page when looking at its layout. The point of using Lorem Ipsum is that it has a more-or-less normal distribution of letters, as opposed to using 'Content here, content here', making it look like readable English. Many desktop publishing packages and web page editors now use Lorem Ipsum as their default model text, and a search for 'lorem ipsum' will uncover many web sites still in their infancy. Various versions have evolved over the years, sometimes by accident, sometimes on purpose (injected humour and the like).</p>
      <p>Contrary to popular belief, Lorem Ipsum is not simply random text. It has roots in a piece of classical Latin literature from 45 BC, making it over 2000 years old. Harold Penwick, a Latin professor at Linfield Ridge College, looked up one of the more obscure Latin words, consectetur, from a Lorem Ipsum passage, and going through the cites of the word in classical literature, discovered the undoubtable source. Lorem Ipsum comes from sections 1.10.32 and 1.10.33 of "de Finibus Bonorum et Malorum" structures, to generate Lorem Ipsum which looks reasonable. The generated Lorem Ipsum is therefore always free from repetition, injected humour, or non-characteristic words etc.</p>
    </section>

    <div class="signature" role="img" aria-label="Handwritten signature of the sender"></div>

    <div class="ghost-name">Brightfield Ventures Inc.</div>

    <svg class="swoosh" viewBox="0 0 524 150" preserveAspectRatio="none" aria-hidden="true">
      <defs>
        <linearGradient id="redBand" x1="0" y1="0" x2="1" y2="0">
          <stop offset="0" stop-color="#d3222a"/>
          <stop offset=".6" stop-color="#e98a8c"/>
          <stop offset="1" stop-color="#ffffff"/>
        </linearGradient>
        <linearGradient id="navyBand" x1="0" y1="0" x2="1" y2="0">
          <stop offset="0" stop-color="#1a2775"/>
          <stop offset="1" stop-color="#2a3ea3"/>
        </linearGradient>
      </defs>
      <path d="M0 40 C140 70 260 130 524 110 L524 150 L0 150 Z" fill="url(#redBand)"/>
      <path d="M0 60 C150 90 270 150 524 130 L524 150 L0 150 Z" fill="#ffffff"/>
      <path d="M0 68 C150 100 280 158 524 138 L524 150 L0 150 Z" fill="url(#navyBand)"/>
    </svg>
  </main>
</body>
</html>
```